Rapid Pulse Tiny Track Karts

We are looking for a full web site for our race car category that allows us to edit and update some of the content. We would like the site to feel modern and attractive with the following features: 1. Event calender (with the ability for us to update) 2. Social media/ clip wave links 3. photo gallery (with the ability for us to update) 4. Member area with log in access (controlled access) - this area to include access to category regulations for up to 5 types of cars separately 5. Championship ladder for up to 5 different groups 6. sponsor page and sponsors scrolling across bottom of all pages. Please find attached our logo to be used and for reference on color/ style 7. page to show merchandise but no need for a store.

Industry/Entity Type

Motor racing category

Coding

Coded - Design and coding required

Number of Pages Required

5+ page

Colors
0054AA
0677BA
7BADD7
CADEEF
E8F1F8
FFF300
FFF600
FEFA6F
FFFEC7
FFFEE8
EB3D1F
EC4F4E
F09395
F8D3D4
FCEDEE

Requirements
Must have
• Ability to update calender/photo gallery/championship ladder including points/ notice board - Members section

```html
<!DOCTYPE html>
<html lang="en">
<head>
<meta charset="utf-8">
<title>Rapid Pulse Tiny Track Karts</title>
<link href="https://fonts.googleapis.com/css2?family=Russo+One&family=Mulish:wght@400;500;600;700&display=swap" rel="stylesheet">
<style>
:root{
  --nav:#184a91;
  --royal:#0c3a9d;
  --indigo:#2335a1;
  --red:#f5141c;
  --yellow:#fdd835;
  --ink:#151515;
  --grey-panel:#efefef;
  --score-col:#ececec;
  --white:#ffffff;
}
*{margin:0;padding:0;box-sizing:border-box}
html,body{width:1200px;height:5155px;overflow:hidden;background:var(--white)}
body{font-family:"Mulish",sans-serif;color:var(--ink);position:relative}
.abs{position:absolute}
.display{font-family:"Russo One",sans-serif;font-variant:small-caps;letter-spacing:1px}
.btn{position:absolute;background:var(--red);color:var(--white);border-radius:22px;font-size:16px;display:flex;align-items:center;justify-content:center}
.ph{position:absolute}

/* nav */
.site-nav{position:absolute;left:0;top:0;width:1200px;height:112px;background:var(--nav)}
.brand{position:absolute;display:flex;align-items:center;gap:10px;font-weight:700;font-size:22px;white-space:nowrap}
.brand .mark{width:18px;height:18px;background:var(--red)}
.site-nav .brand{left:116px;top:38px;color:var(--white)}
.nav-links{position:absolute;top:46px;left:456px;font-size:14px;color:var(--white)}
.nav-links a{color:var(--white);text-decoration:none;position:absolute;white-space:nowrap}
.nav-links a.active{text-decoration:underline;text-underline-offset:4px}
.login{left:928px;top:37px;width:182px;height:42px;font-size:17px}

/* hero */
.hero{position:absolute;left:0;top:112px;width:1200px;height:720px;background:var(--royal)}
.hero-strip{left:0;top:0;width:1200px;height:158px;background:linear-gradient(180deg,#1b2e5e,#2e4f9a 70%,var(--royal))}
.hero-title{position:absolute;top:250px;width:1200px;text-align:center;color:var(--white);font-size:44px;line-height:52px}
.hero-text{position:absolute;top:372px;width:1200px;text-align:center;color:var(--white);font-size:17px;line-height:30px}
.hero-cta{left:520px;top:450px;width:160px;height:40px}

/* about */
.section-title{position:absolute;font-size:33px;color:var(--ink)}
.about-text{position:absolute;left:113px;top:980px;width:488px;font-size:16px;line-height:29.3px;text-align:justify;color:#333}
.about-circle{left:830px;top:1058px;width:264px;height:264px;border-radius:50%;background:var(--indigo)}
.about-photo{left:646px;top:912px;width:380px;height:370px;border-radius:14px;background:linear-gradient(135deg,#f4f4f4,#e2e3e6)}

/* events */
.event{position:absolute;top:1578px;width:340px}
.event .img{height:238px;position:relative}
.event .tag{position:absolute;right:0;top:0;background:var(--yellow);font-size:13px;padding:6px 12px}
.event .name{margin-top:18px;margin-left:4px;font-size:18px;font-weight:600;letter-spacing:.5px}

/* ladder */
.ladder{left:234px;top:2072px;width:732px;height:384px;border-radius:22px;background:var(--white);box-shadow:0 10px 40px rgba(0,0,0,.14);overflow:hidden}
.ladder-head{position:absolute;left:0;top:0;width:732px;height:68px;background:var(--indigo);color:var(--white);font-size:18px}
.ladder-head span,.ladder-row span{position:absolute}
.score-col{left:370px;top:68px;width:164px;height:316px;background:var(--score-col)}
.ladder-row{position:absolute;left:0;width:732px;font-size:18px}

/* sponsors */
.sponsor{position:absolute;top:2740px;width:200px;text-align:center;color:#333;font-size:20px;letter-spacing:1px}

/* gallery */
.tile{position:absolute;border-radius:4px}
.view-more{left:520px;top:3914px;width:162px;height:40px}

/* merchandise */
.merch-panel{left:112px;top:4210px;width:976px;height:440px;background:var(--grey-panel)}
.merch-active{left:76px;top:4238px;width:450px;height:74px;background:var(--yellow)}
.merch-item{position:absolute;left:152px;font-size:27px;font-weight:500;white-space:nowrap}

/* footer */
.footer-links{position:absolute;top:4768px;font-size:16px;line-height:29px;color:#222}
.email{left:768px;top:4768px;width:320px;height:42px;border:1.5px solid #555;color:#999;font-size:16px;padding:10px 22px}
.submit{left:768px;top:4834px;width:160px;height:42px}
.copyright{position:absolute;top:5116px;width:1200px;text-align:center;color:var(--white);font-size:14px}
</style>
</head>
<body>

<header class="site-nav">
  <div class="brand"><span class="mark"></span>Rapid Pulse</div>
  <nav class="nav-links">
    <a class="active" style="left:0">Home</a>
    <a style="left:85px">Event</a>
    <a style="left:168px">Gallery</a>
    <a style="left:258px">Sponsor</a>
    <a style="left:356px">Merchandise</a>
  </nav>
  <div class="btn login">Member Log In</div>
</header>

<section class="hero">
  <div class="ph hero-strip" role="img" aria-label="Row of miniature race cars seen from above"></div>
  <h1 class="hero-title display">Rapid Pulse Tiny Track<br>Karts</h1>
  <p class="hero-text">Lorem ipsum dolor sit amet, consectetur<br>adipiscing elit, sed do eiusmod labore et dolore.</p>
  <div class="btn hero-cta">Get Started</div>
</section>

<svg class="abs" style="left:0;top:600px" width="1200" height="240" viewBox="0 600 1200 240" aria-hidden="true">
  <polygon fill="#ffffff" points="0,762 164,684 490,778 760,614 1126,790 1200,812 1200,840 0,840"/>
  <polygon fill="#fdd835" points="104,712 164,680 470,760 490,778 164,696"/>
  <polygon fill="#fdd835" points="730,626 760,610 1126,790 1126,808 760,626"/>
</svg>

<section>
  <h2 class="section-title display" style="left:113px;top:912px">About Us</h2>
  <p class="about-text">Lorem ipsum dolor sit amet, consectetur adipiscing elit, sed do eiusmod tempor incididunt ut labore et dolore magna aliqua. Quis ipsum suspendisse ultrices gravida. Risus commodo viverra maecenas accumsan lacus vel facilisis. Lorem ipsum dolor sit amet, consectetur adipiscing elit, sed do eiusmod tempor incididunt ut labore et dolore magna aliqua. Quis ipsum suspendisse ultrices gravida. Risus commodo viverra maecenas accumsan lacus vel facilisis.</p>
  <div class="btn" style="left:113px;top:1275px;width:160px;height:40px">Read More</div>
  <div class="ph about-circle"></div>
  <div class="ph about-photo" role="img" aria-label="Twelve toy cars arranged in a grid on a white surface"></div>
</section>

<section>
  <h2 class="section-title display" style="left:113px;top:1458px">Upcoming Events</h2>
  <article class="event" style="left:72px">
    <div class="img" role="img" aria-label="Tyre barrier beside a racing track" style="background:linear-gradient(160deg,#8a9494,#3aa3a0 55%,#2c8f8c)"><span class="tag">28 Oct 2023</span></div>
    <div class="name">Rapid Pulse Maniater Race</div>
  </article>
  <article class="event" style="left:432px">
    <div class="img" role="img" aria-label="Spectators watching miniature cars race on a track" style="background:linear-gradient(180deg,#4a4e58,#e9e9ec 45%,#3a3c40)"><span class="tag">28 Oct 2023</span></div>
    <div class="name">Rapid Pulse Maniater Race</div>
  </article>
  <article class="event" style="left:791px">
    <div class="img" role="img" aria-label="Curved racing track with kerbs" style="background:linear-gradient(170deg,#cfcfd2,#4a4a50 45%,#2e2e33)"><span class="tag">28 Oct 2023</span></div>
    <div class="name">Rapid Pulse Maniater Race</div>
  </article>
</section>

<section>
  <h2 class="section-title display" style="left:0;width:1200px;text-align:center;top:1982px">Championship Ladder</h2>
  <div class="abs ladder">
    <div class="ladder-head">
      <span style="left:56px;top:22px">Champions</span>
      <span style="left:420px;top:22px">Score</span>
      <span style="left:606px;top:22px">Rank</span>
    </div>
    <div class="abs score-col"></div>
    <div class="ladder-row" style="top:112px"><span style="left:38px">Rapid Pulse Group 1</span><span style="left:428px">580</span><span style="left:612px">2nd</span></div>
    <div class="ladder-row" style="top:164px"><span style="left:38px">Rapid Pulse Group 2</span><span style="left:428px">684</span><span style="left:612px">1st</span></div>
    <div class="ladder-row" style="top:215px"><span style="left:38px">Rapid Pulse Group 3</span><span style="left:428px">654</span><span style="left:612px">3rd</span></div>
    <div class="ladder-row" style="top:267px"><span style="left:38px">Rapid Pulse Group 4</span><span style="left:428px">585</span><span style="left:612px">4th</span></div>
    <div class="ladder-row" style="top:318px"><span style="left:38px">Rapid Pulse Group 5</span><span style="left:428px">250</span><span style="left:612px">5th</span></div>
  </div>
</section>

<section>
  <h2 class="section-title display" style="left:0;width:1200px;text-align:center;top:2580px">Our Sponsors</h2>
  <div class="sponsor" style="left:62px">Velo Works</div>
  <div class="sponsor" style="left:284px;font-weight:700">Swiftline</div>
  <div class="sponsor" style="left:508px">Gearmark</div>
  <div class="sponsor" style="left:734px">Torque House</div>
  <div class="sponsor" style="left:954px">Apex Motor</div>
  <div class="btn" style="left:520px;top:2860px;width:162px;height:40px">Read More</div>
</section>

<svg class="abs" style="left:0;top:2960px" width="1200" height="1072" viewBox="0 2960 1200 1072" aria-hidden="true">
  <polygon fill="#2335a1" points="0,3030 110,3080 492,3016 680,3112 1126,2978 1200,2978 1200,4032 0,4032"/>
  <polygon fill="#fdd835" points="100,3062 470,2998 492,3016 110,3080"/>
  <polygon fill="#fdd835" points="680,3094 1126,2960 1126,2978 680,3112"/>
</svg>

<section>
  <h2 class="section-title display" style="left:0;width:1200px;text-align:center;top:3178px;color:#fff">Gallery</h2>
  <div class="tile" style="left:112px;top:3274px;width:232px;height:392px;background:linear-gradient(180deg,#f2c94c,#f59ab0 60%,#f08fb0)" role="img" aria-label="Vintage toy car on a pink and yellow background"></div>
  <div class="tile" style="left:360px;top:3274px;width:314px;height:188px;background:linear-gradient(160deg,#3a4a40,#c9a630 55%,#2b2f2a)" role="img" aria-label="Yellow toy taxi among model cars"></div>
  <div class="tile" style="left:360px;top:3478px;width:314px;height:188px;background:linear-gradient(180deg,#3a5a8a,#8aa2c0 50%,#2c2f36)" role="img" aria-label="Miniature rally car on a beach"></div>
  <div class="tile" style="left:690px;top:3274px;width:398px;height:298px;background:linear-gradient(170deg,#a8c04a,#6d8a2a 55%,#4a5a22)" role="img" aria-label="Black sports car model on a green blurred background"></div>
  <div class="tile" style="left:112px;top:3682px;width:562px;height:176px;background:linear-gradient(120deg,#c0392b,#2e6fc2 35%,#e3b02a 65%,#27823f)" role="img" aria-label="Pile of colourful toy cars"></div>
  <div class="tile" style="left:690px;top:3588px;width:232px;height:270px;background:linear-gradient(180deg,#e9c1b5,#e4bcae)" role="img" aria-label="Mint green small toy car on a peach background"></div>
  <div class="tile" style="left:936px;top:3588px;width:152px;height:270px;background:linear-gradient(180deg,#3a3a3a,#3f9a3a 40%,#bdbdbd 70%,#2a2a2a)" role="img" aria-label="Close up of a white sports car model"></div>
  <div class="btn view-more">View More</div>
</section>

<section>
  <h2 class="section-title display" style="left:0;width:1200px;text-align:center;top:4108px">Merchandise</h2>
  <div class="abs merch-panel"></div>
  <div class="abs merch-active"></div>
  <div class="merch-item" style="top:4256px">Rapid Pulse Mechandise 1</div>
  <div class="merch-item" style="top:4325px">Rapid Pulse Mechandise 2</div>
  <div class="merch-item" style="top:4385px">Rapid Pulse Mechandise 3</div>
  <div class="merch-item" style="top:4445px">Rapid Pulse Mechandise 4</div>
  <div class="merch-item" style="top:4505px">Rapid Pulse Mechandise 5</div>
  <div class="merch-item" style="top:4565px">Rapid Pulse Mechandise 6</div>
  <div class="ph" style="left:580px;top:4288px;width:160px;height:330px;background:linear-gradient(180deg,#ffffff,#dcdcdc);border-radius:30px 30px 8px 8px" role="img" aria-label="White team t-shirt"></div>
  <div class="ph" style="left:836px;top:4288px;width:190px;height:330px;background:linear-gradient(180deg,#2a2a2a,#111);border-radius:30px 30px 8px 8px" role="img" aria-label="Black team t-shirt"></div>
</section>

<footer>
  <div class="brand" style="left:112px;top:4784px;color:var(--royal)"><span class="mark"></span>Rapid Pulse</div>
  <div class="abs" style="left:112px;top:4866px;display:flex;align-items:center;gap:10px;font-size:15px">
    <span style="width:34px;height:34px;border-radius:50%;background:var(--red);display:block"></span>clip wave
  </div>
  <div class="footer-links" style="left:396px">Home<br>About Us<br>Shop<br>Extension<br>Contact Us</div>
  <div class="footer-links" style="left:564px">Support<br>FAQ<br>Terms &amp; Conditions<br>Privacy Policy</div>
  <div class="abs email">Email</div>
  <div class="btn submit">Submit</div>
</footer>

<svg class="abs" style="left:0;top:4950px" width="1200" height="205" viewBox="0 4950 1200 205" aria-hidden="true">
  <polygon fill="#0c3a9d" points="0,5020 200,4994 480,5090 1126,4960 1200,4960 1200,5155 0,5155"/>
  <polygon fill="#fdd835" points="40,5080 200,4994 220,5004 70,5082"/>
  <polygon fill="#fdd835" points="690,5070 1126,4960 1126,4980 720,5076"/>
</svg>
<p class="copyright">© Copyrights 2023 Rapid Pulse Tiny Track Karts | All Rights Reserved</p>

</body>
</html>
```